Creative, fresh business card design for Ripplecraft Facades

We need a fresh, creative business card design for Ripplecraft Facades. We are the manufacturer of Ripplecraft Facades in Australia. Wall panels are 2400 x 1200mm panels made from MDF and feature 3D patterns on the face of the panel. The colours to be used are green, silver/grey and white RGB
Red 187
Green 207
Blue 65.

An idea is to possibly use a watermark of one of our designs as a background (like on the "Grids" design on the left hand side of page 2 of our brochure).

Target Market(s)

Interior designers, architects, builders and home renovators

Industry/Entity Type

Business

Contact Information for Business Card

Details to go on the card are:
Our logo (attached),
Slogan: "Decorative panels for interiors and exteriors",
Contact name,
Position,
Mobile phone number,
Business address,
Business phone,
Business fax,
Website and
Email address.

I have attached a few images of our panels and our brochure for reference.

The colours of the business card should feature our logo colours which are: RGB
Red 187
Green 207
Blue 65

Requirements
Must have
• Very modern fonts and design. Some of the designs shown especially the "Prisms" design which is a popular design.
Nice to have
• Creative but simple design. Very contemporary.
Should not have
• Anything ornate or old fashioned.

```html
<!DOCTYPE html>
<html lang="en">
<head>
<meta charset="utf-8">
<title>Ripplecraft Facades — Business Card</title>
<link href="https://fonts.googleapis.com/css2?family=Open+Sans:wght@300;400;700&display=swap" rel="stylesheet">
<style>
  :root {
    --brand-green: rgb(187, 207, 65);
    --silver: #a7a8ab;
    --ink: #4a4a4c;
    --ink-soft: #8c8c8f;
    --paper: #ffffff;
    --backdrop: #e9eaec;
  }
  * { margin: 0; padding: 0; box-sizing: border-box; }
  html, body {
    width: 1200px; height: 1000px; overflow: hidden;
    background: var(--backdrop);
    font-family: "Open Sans", Arial, sans-serif;
  }
  .card {
    position: absolute; left: 100px; top: 215px;
    width: 1000px; height: 570px;
    background: var(--paper);
    box-shadow: 0 10px 30px rgba(0,0,0,.12);
    overflow: hidden;
  }
  .brand {
    position: absolute; left: 90px; top: 118px;
    display: flex; align-items: center; gap: 14px;
  }
  .brand-square { width: 34px; height: 34px; background: var(--brand-green); }
  .brand-name {
    font-weight: 700; font-size: 44px; color: var(--brand-green);
    letter-spacing: -1px; line-height: 1;
  }
  .company-band {
    position: absolute; left: 405px; top: 112px;
    width: 330px; height: 34px; background: var(--silver);
    color: #fff; font-weight: 300; font-size: 25px;
    padding-left: 12px; line-height: 34px;
  }
  .slogan {
    position: absolute; left: 412px; top: 152px;
    color: var(--ink-soft); font-weight: 400; font-size: 18px;
    line-height: 20px; letter-spacing: 2px;
  }
  .person {
    position: absolute; left: 150px; top: 230px;
    font-weight: 700; font-size: 38px; color: var(--ink); line-height: 1;
  }
  .person .surname { color: var(--brand-green); }
  .accent-rule {
    position: absolute; left: 375px; top: 283px;
    width: 625px; height: 2px; background: var(--brand-green);
  }
  .role {
    position: absolute; left: 150px; top: 272px;
    font-weight: 700; font-size: 26px; color: var(--silver);
  }
  .contacts {
    position: absolute; left: 150px; top: 340px; list-style: none;
    color: var(--ink); font-size: 25px; font-weight: 400;
  }
  .contacts li { display: flex; align-items: center; height: 36px; }
  .contacts li.gap { margin-top: 26px; }
  .icon { width: 22px; height: 22px; margin-right: 34px; fill: var(--ink); }
  .contacts .phones li { padding-left: 56px; }
  .highlight { color: var(--brand-green); }
</style>
</head>
<body>
  <section class="card" aria-label="Ripplecraft Facades business card">
    <div class="brand">
      <span class="brand-square"></span>
      <span class="brand-name">Ripplecraft</span>
    </div>
    <div class="company-band">Ripplecraft Facades</div>
    <p class="slogan">decorative panels for<br>interiors &amp; landscapes</p>

    <h1 class="person">Lena <span class="surname">Marsh</span></h1>
    <div class="accent-rule"></div>
    <p class="role">Director</p>

    <ul class="contacts">
      <li>
        <svg class="icon" viewBox="0 0 24 24" aria-hidden="true"><rect x="6" y="2" width="12" height="20" rx="2"/><rect x="8" y="5" width="8" height="12" fill="#fff"/></svg>
        +000 555 010 201
      </li>
      <li>
        <svg class="icon" viewBox="0 0 24 24" aria-hidden="true"><path d="M6 3l4 4-2 3c1 2.5 3.5 5 6 6l3-2 4 4-3 3C10 21 3 14 3 6z"/></svg>
        +000 555 010 202
      </li>
      <li>
        <svg class="icon" viewBox="0 0 24 24" aria-hidden="true"><rect x="7" y="2" width="10" height="7"/><rect x="3" y="9" width="18" height="9" rx="1"/><rect x="7" y="15" width="10" height="7"/></svg>
        +000 555 010 203
      </li>
      <li class="gap">
        <svg class="icon" viewBox="0 0 24 24" aria-hidden="true"><rect x="2" y="5" width="20" height="14"/><path d="M2 5l10 8 10-8" fill="none" stroke="#fff" stroke-width="2"/></svg>
        lena@ripplecraft-mail.com
      </li>
      <li>
        <svg class="icon" viewBox="0 0 24 24" aria-hidden="true"><circle cx="14" cy="10" r="6" fill="none" stroke="#4a4a4c" stroke-width="3"/><path d="M9.5 14.5L3 21" stroke="#4a4a4c" stroke-width="3.5"/></svg>
        www.<span class="highlight">ripplecraftpanels</span>.com
      </li>
    </ul>
  </section>
</body>
</html>
```